Stationery Design Project for Nimbora, Chicago

Nimbora, a street parking application which helps car drivers find a street parking spot by offering an ideal path along which to look for parking. This path is calculated by our algorithm based on data (e.g. historical data, baseball games schedule, etc.). Along this path the driver will find a spot and will also save 70% of the search time. Customer we target is reg. between 21 and 45 yo.

We envision something young, fresh, bright and original. Slightly abstract maybe. It should represent the idea and elements of finding street parking in the city, e.g. car(s), parking spot, people, city, etc. (just ideas!).

Logo is attached.

Requirement:
- Business Cards (2 Sided Full Color CMYK)
- Letterhead (1 Sided Full Color CMYK)
- Envelope (1 Sided Full Color CMYK)
- Sticker (1 Sided Full Color CMYK), round with a 2inch diameter.

Reason: We're starting to get more and more designs and need more time to look into all of them. Very exciting!! Thanks to everybody!

Hi all, we're in the process of selecting our favs. Though choices!!! Really good submissions. Will keep you posted and sorry for the delay.

Target Market(s)

Car drivers and owners between 21 and 45

Industry/Entity Type

Parking

Requirements
Must have
• Sticker should be round and include company URL nimbora.com and the new logo which we will attach soon.
Should not have
• Should not be too serious or boring.

```html
<!DOCTYPE html>
<html lang="en">
<head>
<meta charset="utf-8">
<title>Nimbora – Business Cards</title>
<link rel="stylesheet" href="https://fonts.googleapis.com/css2?family=Open+Sans:wght@400;600;700&display=swap">
<style>
  :root {
    --backdrop: #e4e5e7;
    --card-white: #ffffff;
    --card-grey: #5c5c5e;
    --ink: #3a3a3c;
    --ink-soft: #555557;
    --band-dark: #1c1c1e;
    --band-mid: #6a6a6c;
    --brand-blue: #1a63c9;
    --brand-blue-deep: #1c3fa8;
    --brand-blue-light: #3f8ae6;
    --black: #0c0c0c;
    --white: #ffffff;
  }
  * { margin: 0; padding: 0; box-sizing: border-box; }
  html, body {
    width: 1200px; height: 954px; overflow: hidden;
    background: var(--backdrop);
    font-family: "Open Sans", Arial, sans-serif;
  }
  .card {
    position: absolute; top: 78px;
    width: 456px; height: 798px;
    border-radius: 24px; overflow: hidden;
    box-shadow: 0 6px 18px rgba(0,0,0,.25);
  }
  .card--front { left: 77px; background: var(--card-white); }
  .card--back  { left: 632px; background: var(--card-grey); }
  .card svg.art { position: absolute; inset: 0; width: 456px; height: 798px; }

  .wordmark {
    position: absolute; left: 0; right: 0; top: 262px;
    text-align: center;
    font-weight: 700; font-size: 76px; line-height: 1;
    letter-spacing: -1px;
  }
  .card--front .wordmark { color: var(--ink); }
  .card--back  .wordmark { color: var(--white); }

  .person { position: absolute; left: 40px; top: 400px; color: var(--ink-soft); }
  .person__name { font-weight: 700; font-size: 30px; line-height: 1.1; }
  .person__role { font-size: 21px; margin-top: 4px; }

  .contacts {
    position: absolute; left: 40px; top: 578px;
    list-style: none; color: var(--ink-soft);
    font-size: 19px; line-height: 27px;
  }
  .contacts b { font-weight: 700; }
  .address {
    position: absolute; left: 40px; top: 711px;
    color: var(--ink-soft); font-size: 19px; line-height: 27px;
  }

  .parking-photo {
    position: absolute; left: 89px; top: 253px;
    width: 266px; height: 467px;
    background: linear-gradient(170deg, #8f9397 0%, #6f767c 45%, #9aa0a4 100%);
    -webkit-mask-image: linear-gradient(to right, transparent 0, #000 22%, #000 80%, transparent 100%);
            mask-image: linear-gradient(to right, transparent 0, #000 22%, #000 80%, transparent 100%);
  }
  .website {
    position: absolute; left: 50px; top: 741px;
    color: var(--white); font-size: 21px; letter-spacing: 2px;
  }
</style>
</head>
<body>

<section class="card card--front">
  <svg class="art" viewBox="0 0 456 798" aria-hidden="true">
    <defs>
      <linearGradient id="frontBandDark" x1="0" x2="1">
        <stop offset="0" stop-color="var(--band-dark)"/>
        <stop offset="1" stop-color="var(--band-mid)"/>
      </linearGradient>
      <linearGradient id="frontBandBlue" x1="0" x2="1">
        <stop offset="0" stop-color="var(--brand-blue-light)"/>
        <stop offset="1" stop-color="var(--brand-blue-deep)"/>
      </linearGradient>
      <linearGradient id="frontCorner" x1="0" y1="0" x2="0" y2="1">
        <stop offset="0" stop-color="var(--brand-blue)"/>
        <stop offset="1" stop-color="var(--brand-blue-deep)"/>
      </linearGradient>
    </defs>
    <rect class="band-dark" x="0" y="68" width="260" height="185" fill="url(#frontBandDark)"/>
    <rect class="band-blue" x="236" y="68" width="220" height="185" fill="url(#frontBandBlue)"/>
    <circle class="band-ring" cx="236" cy="156" r="96" fill="var(--black)"/>
    <circle class="brand-dot" cx="236" cy="156" r="78" fill="var(--brand-blue)"/>
    <path class="corner-wave" d="M456 560 C420 620 380 700 340 798 L456 798 Z" fill="url(#frontCorner)"/>
  </svg>

  <div class="wordmark">Nimbora</div>

  <div class="person">
    <div class="person__name">Your Name</div>
    <div class="person__role">Designation</div>
  </div>

  <ul class="contacts">
    <li><b>p</b> : 123-456-7890</li>
    <li><b>c</b> : 123-456-7890</li>
    <li><b>e</b> : name@website.com</li>
    <li><b>w</b> : www.website.com</li>
  </ul>

  <p class="address">City Name, Street Name,<br>State Name, Country Code</p>
</section>

<section class="card card--back">
  <svg class="art" viewBox="0 0 456 798" aria-hidden="true">
    <defs>
      <linearGradient id="backBandDark" x1="0" x2="1">
        <stop offset="0" stop-color="var(--band-dark)"/>
        <stop offset="1" stop-color="var(--band-mid)"/>
      </linearGradient>
      <linearGradient id="backBandBlue" x1="0" x2="1">
        <stop offset="0" stop-color="var(--brand-blue-light)"/>
        <stop offset="1" stop-color="var(--brand-blue-deep)"/>
      </linearGradient>
      <linearGradient id="backBody" x1="0" y1="0" x2="0" y2="1">
        <stop offset="0" stop-color="var(--black)"/>
        <stop offset=".75" stop-color="#1a1a1a"/>
        <stop offset="1" stop-color="var(--card-grey)"/>
      </linearGradient>
      <linearGradient id="backCorner" x1="0" y1="0" x2="0" y2="1">
        <stop offset="0" stop-color="var(--brand-blue)"/>
        <stop offset="1" stop-color="var(--brand-blue-deep)"/>
      </linearGradient>
    </defs>
    <rect class="body-shade" x="0" y="253" width="456" height="480" fill="url(#backBody)"/>
    <rect class="band-dark" x="0" y="68" width="260" height="185" fill="url(#backBandDark)"/>
    <rect class="band-blue" x="236" y="68" width="220" height="185" fill="url(#backBandBlue)"/>
    <circle class="band-ring" cx="236" cy="156" r="96" fill="var(--black)"/>
    <circle class="brand-dot" cx="236" cy="156" r="78" fill="var(--brand-blue)"/>
    <path class="corner-wave" d="M456 560 C420 620 380 700 340 798 L456 798 Z" fill="url(#backCorner)"/>
  </svg>

  <div class="parking-photo" role="img" aria-label="Photo of a busy car park seen from above, rows of parked cars"></div>

  <div class="wordmark">Nimbora</div>

  <div class="website">www.website.com</div>
</section>

</body>
</html>
```